Gleam Fellows

I need a flyer and business cards to hand out at office buildings and country clubs introducing my new auto detailing business, GLEAM FELLOWS. Call or text 913-555-0184 for an appointment. Complete auto detailing done at their place or mine, and we offer pick -up and drop-off, if needed. I believe the flyer needs a car on it. Black, blue, and pink are my preferred colors. While you go about your day's business, whether playing 18 holes of golf or putting in 8 hours at the office, we will have your ride shining like a new penny when you're ready to roll!

```html
<!DOCTYPE html>
<html lang="en">
<head>
<meta charset="utf-8">
<title>Gleam Fellows – Flyer</title>
<link rel="stylesheet" href="https://fonts.googleapis.com/css2?family=Orbitron:wght@700;900&family=Roboto+Condensed:ital,wght@1,700;1,800;1,900&family=Kanit:ital,wght@1,500;1,600&display=swap">
<style>
  :root{
    --ink:#000;
    --stage:#07111d;
    --blue:#1a8cff;
    --pink:#e414c4;
    --white:#ffffff;
  }
  *{margin:0;padding:0;box-sizing:border-box}
  html,body{width:1200px;height:1200px;overflow:hidden;background:var(--stage)}
  .flyer{position:absolute;left:152px;top:20px;width:896px;height:1160px;background:var(--ink);overflow:hidden}
  .art{position:absolute;left:0;top:0;width:896px;height:1160px}
  .abs{position:absolute}
  .display{font-family:"Orbitron",sans-serif;font-weight:900;transform:skewX(-14deg);transform-origin:left bottom}
  .title{line-height:1;letter-spacing:1px}
  .title-top{left:60px;top:52px;font-size:80px;color:var(--blue)}
  .title-bottom{left:60px;top:120px;font-size:66px;color:var(--pink)}
  .tagline{left:58px;top:206px;font-size:24px;line-height:30px;color:var(--white);letter-spacing:1px}
  .intro{left:57px;top:318px;font-family:"Kanit",sans-serif;font-style:italic;font-weight:500;font-size:17px;line-height:22px;color:var(--pink)}
  .promise{left:57px;top:370px;font-family:"Kanit",sans-serif;font-style:italic;font-weight:600;font-size:17px;line-height:18px;color:var(--blue);text-transform:uppercase}
  .brand-mark{left:600px;top:606px;display:flex;align-items:center;gap:10px;font-family:"Orbitron",sans-serif;font-weight:900;font-size:25px;color:var(--blue)}
  .brand-dot{width:22px;height:22px;border-radius:50%;background:var(--blue)}
  .headline{left:84px;top:770px;font-size:31px;line-height:36px;color:var(--white);letter-spacing:1px}
  .label{font-size:15px;letter-spacing:2px;color:var(--ink);text-align:center;width:200px}
  .label-interior{left:404px;top:848px}
  .label-exterior{left:626px;top:848px}
  .service-line{left:78px;top:898px;width:741px;text-align:center;font-family:"Roboto Condensed",sans-serif;font-style:italic;font-weight:900;font-size:16px;letter-spacing:4px;color:var(--pink);text-transform:uppercase}
  .feature{font-family:"Roboto Condensed",sans-serif;font-style:italic;font-weight:900;font-size:31px;line-height:28px;color:var(--white);text-transform:uppercase;white-space:nowrap}
  .feature-place{left:170px;top:952px}
  .feature-pickup{left:534px;top:952px}
  .cta{left:72px;top:1058px;font-family:"Roboto Condensed",sans-serif;font-style:italic;font-weight:900;font-size:29px;color:var(--blue);text-transform:uppercase;white-space:nowrap}
  .cta span{color:var(--pink)}
  .cta-sub{left:74px;top:1098px;font-family:"Roboto Condensed",sans-serif;font-style:italic;font-weight:700;font-size:11px;letter-spacing:2px;color:var(--white);text-transform:uppercase;white-space:nowrap}
  .hours{left:561px;top:1062px;width:258px;font-size:12px;letter-spacing:1px;color:var(--blue);text-transform:uppercase;text-align:right}
  .phone{left:561px;top:1072px;width:258px;text-align:right;font-family:"Roboto Condensed",sans-serif;font-style:italic;font-weight:900;font-size:44px;color:var(--white)}
</style>
</head>
<body>
<main class="flyer">
  <svg class="art" viewBox="0 0 896 1160" xmlns="http://www.w3.org/2000/svg">
    <defs>
      <linearGradient id="heroFade" x1="0" y1="0" x2="0" y2="1">
        <stop offset="0" stop-color="#b015b8"/>
        <stop offset="0.55" stop-color="#6d1490"/>
        <stop offset="1" stop-color="#000"/>
      </linearGradient>
      <radialGradient id="carTone" cx="0.45" cy="0.55" r="0.55">
        <stop offset="0" stop-color="#4a4a4f"/>
        <stop offset="0.45" stop-color="#222226"/>
        <stop offset="0.8" stop-color="#0a0a0b"/>
        <stop offset="1" stop-color="#000" stop-opacity="0"/>
      </radialGradient>
      <radialGradient id="glow" cx="0" cy="0.5" r="0.6">
        <stop offset="0" stop-color="#0a5fbf" stop-opacity="0.6"/>
        <stop offset="1" stop-color="#000" stop-opacity="0"/>
      </radialGradient>
      <linearGradient id="photoGrey" x1="0" y1="0" x2="1" y2="1">
        <stop offset="0" stop-color="#5b5b60"/>
        <stop offset="1" stop-color="#18181a"/>
      </linearGradient>
    </defs>

    <rect x="0" y="300" width="420" height="260" fill="url(#glow)"/>

    <path d="M626 0H896V640H520L556 180Z" fill="url(#heroFade)" role="img" aria-label="Photo of a gloved hand polishing a car headlight with a buffer, tinted pink"/>
    <line x1="626" y1="0" x2="556" y2="182" stroke="var(--blue)" stroke-width="5"/>

    <rect x="-80" y="430" width="680" height="350" fill="url(#carTone)" role="img" aria-label="Photo of a glossy black sports car"/>

    <circle cx="546" cy="263" r="82" fill="url(#photoGrey)" stroke="var(--blue)" stroke-width="6" role="img" aria-label="Photo of a car interior being vacuumed"/>
    <circle cx="503" cy="426" r="103" fill="url(#photoGrey)" stroke="var(--blue)" stroke-width="6" role="img" aria-label="Photo of a steering wheel being cleaned with a sponge"/>

    <path d="M410 711H630L612 876H394Z" fill="url(#photoGrey)" role="img" aria-label="Photo of a brush cleaning a dashboard air vent"/>
    <path d="M630 711H851L833 876H613Z" fill="url(#photoGrey)" role="img" aria-label="Photo of a car panel being machine polished"/>
    <path d="M398 837H610L606 876H394Z" fill="var(--pink)"/>
    <path d="M617 837H838L833 876H613Z" fill="var(--blue)"/>

    <line x1="78" y1="891" x2="819" y2="891" stroke="var(--blue)" stroke-width="1.5"/>
    <line x1="78" y1="928" x2="819" y2="928" stroke="var(--blue)" stroke-width="1.5"/>
    <line x1="78" y1="1042" x2="819" y2="1042" stroke="var(--blue)" stroke-width="1.5"/>

    <circle cx="109" cy="981" r="33" fill="var(--pink)" stroke="var(--blue)" stroke-width="5"/>
    <path d="M94 998V978L109 965L124 978V998H113V986H105V998Z" fill="none" stroke="var(--white)" stroke-width="2" stroke-linejoin="round"/>
    <circle cx="472" cy="981" r="33" fill="var(--pink)" stroke="var(--blue)" stroke-width="5"/>
    <path d="M456 975H484M478 968L485 975L478 982M488 988H460M466 981L459 988L466 995" fill="none" stroke="var(--white)" stroke-width="2" stroke-linecap="round" stroke-linejoin="round"/>
  </svg>

  <h1 class="abs display title title-top">GLEAM</h1>
  <div class="abs display title title-bottom">FELLOWS</div>
  <p class="abs display tagline">LUXURY MOBILE<br>DETAILING. ON<br>YOUR SCHEDULE.</p>
  <p class="abs intro">While you're busy with work or golf,<br>we'll handle the shine.</p>
  <p class="abs promise">Your ride will be spotless<br>&amp; ready when you are.</p>

  <div class="abs brand-mark"><span class="brand-dot"></span>Gleam Fellows</div>

  <h2 class="abs display headline">COMPLETE<br>AUTO<br>DETAILING</h2>
  <div class="abs display label label-interior">INTERIOR</div>
  <div class="abs display label label-exterior">EXTERIOR</div>

  <p class="abs service-line">Fast, friendly,&nbsp; professional service</p>

  <p class="abs feature feature-place">Service at your<br>place or ours</p>
  <p class="abs feature feature-pickup">Pick-up &amp;<br>drop-off available</p>

  <p class="abs cta">Call or text for <span>an appointment</span></p>
  <p class="abs cta-sub">Let us handle your car care while you handle your day</p>
  <p class="abs display hours">Hours are flexible</p>
  <p class="abs phone">913-555-0184</p>
</main>
</body>
</html>
```